Velk Partners Building Business Cards

We need a business card that reflects our business as "Solar Experts" in San Diego. Browse our website www.velkpartners.example our License needs to be displayed as "CSLB# 3867140" our phone number is (619) 555-0187

Save thousands on your electric bills and increase the value of your home while helping to protect the environment. Our solar installation experts will help you design the system that's right for you, using only the highest quality equipment that will look great and give you ideal performance. Our goal is to make you energy independent, and get your electric bill to 0.

Paul Osterby
(619) 555-0187
paul@velkpartners.example

Target Market(s)

Home owners in san diego looking for solar

Industry/Entity Type

Solar Energy

Contact Information for Business Card

Paul Osterby
(619) 555-0187
paul@velkpartners.example

Font styles to use
Other font styles liked:
• Use our logo font

Requirements
Must have
• License needs to be displayed as "CSLB# 3867140" our phone number is (619) 555-0187
Nice to have
• Real images of rooftop home solar in san diego
Should not have
• our business address

```html
<!DOCTYPE html>
<html lang="en">
<head>
<meta charset="utf-8">
<title>Velk Partners Building – Business Cards</title>
<link href="https://fonts.googleapis.com/css2?family=Roboto:wght@400;500;700&display=swap" rel="stylesheet">
<style>
  :root {
    --navy: #263f82;
    --navy-deep: #1f356f;
    --gold: #f0a90f;
    --paper: #f7f7f6;
    --ink: #2b2f3a;
    --backdrop: #a9a6a7;
    --white: #ffffff;
  }
  * { box-sizing: border-box; margin: 0; padding: 0; }
  html, body { width: 1200px; height: 1200px; overflow: hidden; }
  body {
    background: var(--backdrop);
    font-family: "Roboto", Arial, sans-serif;
    position: relative;
  }
  .card {
    position: absolute;
    width: 712px;
    height: 418px;
    border-radius: 22px;
    overflow: hidden;
  }
  /* Front */
  .card-front { left: 238px; top: 118px; background: var(--navy); }
  .front-photo {
    position: absolute; inset: 0;
    background: linear-gradient(160deg, #2d4a92 0%, #263f82 55%, #213876 100%);
  }
  .front-brand {
    position: absolute; top: 68px; left: 0; right: 0;
    text-align: center;
    font-weight: 700; font-size: 50px; letter-spacing: -0.5px;
    color: var(--white);
  }
  .process-title {
    position: absolute; top: 205px; left: 0; right: 0;
    text-align: center;
    font-weight: 500; font-size: 22px; letter-spacing: 4px;
    color: var(--white);
  }
  .process-rule {
    position: absolute; top: 218px; width: 54px; height: 3px;
    background: var(--gold);
  }
  .process-rule.left { left: 175px; }
  .process-rule.right { left: 484px; }
  .process-link {
    position: absolute; top: 289px; left: 170px; width: 380px;
    border-top: 2px dotted var(--white);
  }
  .step {
    position: absolute; top: 252px; width: 160px; margin-left: -41px;
    text-align: center;
  }
  .step-box {
    width: 78px; height: 76px; margin: 0 auto;
    background: var(--gold);
    display: flex; align-items: center; justify-content: center;
  }
  .step-label {
    margin-top: 10px;
    font-size: 14px; line-height: 15px; color: var(--white);
  }
  /* Back */
  .card-back { left: 232px; top: 644px; background: var(--paper); }
  .back-band {
    position: absolute; left: 0; top: 0; bottom: 0; width: 60px;
    background: var(--navy-deep);
  }
  .back-stripe {
    position: absolute; left: 60px; top: 0; bottom: 0; width: 8px;
    background: var(--gold);
  }
  .back-brand {
    position: absolute; top: 32px; right: 44px;
    font-weight: 700; font-size: 40px; letter-spacing: -0.5px;
    color: var(--navy);
  }
  .person-name {
    position: absolute; left: 99px; top: 192px;
    font-weight: 700; font-size: 26px; letter-spacing: -0.3px;
    color: var(--navy);
  }
  .person-title {
    position: absolute; left: 99px; top: 226px;
    font-size: 17px; color: var(--ink);
  }
  .contact-list {
    position: absolute; left: 99px; top: 279px;
    list-style: none;
  }
  .contact-list li {
    display: flex; align-items: center;
    height: 25px; font-size: 19px; color: var(--ink);
  }
  .contact-list svg { width: 20px; margin-right: 16px; }
  .web-accent { color: var(--gold); }
  .license {
    position: absolute; left: 99px; top: 361px;
    font-size: 18px; color: var(--ink);
  }
</style>
</head>
<body>

<section class="card card-front">
  <div class="front-photo" role="img" aria-label="Photo of rooftop solar panels, tinted blue"></div>
  <div class="front-brand">Velk Partners Building</div>

  <span class="process-rule left"></span>
  <h2 class="process-title">OUR PROCESS</h2>
  <span class="process-rule right"></span>
  <div class="process-link"></div>

  <div class="step" style="left:92px">
    <div class="step-box">
      <svg width="44" height="44" viewBox="0 0 44 44" fill="none" stroke="#263f82" stroke-width="3">
        <circle cx="18" cy="18" r="10"/>
        <line x1="25" y1="25" x2="36" y2="36" stroke-width="6" stroke-linecap="round"/>
      </svg>
    </div>
    <p class="step-label">Site<br>Evaluation</p>
  </div>

  <div class="step" style="left:242px">
    <div class="step-box">
      <svg width="44" height="44" viewBox="0 0 44 44" fill="none" stroke="#263f82" stroke-width="3" stroke-linejoin="round">
        <path d="M10 12 L16 6 L38 30 L38 38 L30 38 Z"/>
        <line x1="14" y1="17" x2="20" y2="11"/>
      </svg>
    </div>
    <p class="step-label">Design &amp;<br>Permitting</p>
  </div>

  <div class="step" style="left:392px">
    <div class="step-box">
      <svg width="46" height="40" viewBox="0 0 46 40" fill="#263f82">
        <rect x="4" y="9" width="36" height="24" rx="3"/>
        <rect x="4" y="14" width="36" height="5" fill="#f0a90f"/>
        <rect x="26" y="24" width="9" height="4" fill="#f0a90f"/>
      </svg>
    </div>
    <p class="step-label">Purchase of<br>Materials</p>
  </div>

  <div class="step" style="left:543px">
    <div class="step-box">
      <svg width="46" height="46" viewBox="0 0 46 46" fill="none" stroke="#263f82" stroke-width="4" stroke-linecap="round">
        <line x1="9" y1="9" x2="36" y2="36"/>
        <line x1="36" y1="9" x2="10" y2="35"/>
        <circle cx="36" cy="9" r="5" stroke-width="3"/>
      </svg>
    </div>
    <p class="step-label">Installation &amp;<br>Commissioning</p>
  </div>
</section>

<section class="card card-back">
  <div class="back-band"></div>
  <div class="back-stripe"></div>
  <div class="back-brand">Velk Partners Building</div>

  <h1 class="person-name">Paul Osterby</h1>
  <p class="person-title">Managing Director</p>

  <ul class="contact-list">
    <li>
      <svg viewBox="0 0 20 16" fill="#f0a90f"><path d="M2 5 Q10 -1 18 5 L15 7 Q10 4 5 7 Z"/><rect x="4" y="8" width="12" height="7" rx="1"/></svg>
      (619) 555-0187
    </li>
    <li>
      <svg viewBox="0 0 20 20" fill="none" stroke="#f0a90f" stroke-width="1.6"><circle cx="10" cy="10" r="8"/><ellipse cx="10" cy="10" rx="3.5" ry="8"/><line x1="2" y1="10" x2="18" y2="10"/></svg>
      paul@velkpartners.example
    </li>
    <li>
      <svg viewBox="0 0 20 14" fill="none" stroke="#f0a90f" stroke-width="1.8"><rect x="1" y="1" width="18" height="12"/><path d="M1 1 L10 8 L19 1"/></svg>
      www.<span class="web-accent">velkpartners</span>.example
    </li>
  </ul>

  <p class="license">License: CSLB# 3867140</p>
</section>

</body>
</html>
```